New iOS App design for Boston Startup

We are looking for a new app design for our iPhone app. The current app's design feels outdated and we like to add lots of new functionality and a new navigation as well. A complete overhaul therefore!
We want you to design 5 screens that will have changed the most. The complete wireframes of these 5 pages are attached in the requirements document.
Once the winning design is selected we will award the winner with the designing all other screens (40-50 screens based on the same design). This will be a separate project worth $1000. The winning designer can get more follow up work if both sides are happy about the cooperation.
We will give feedback as soon as the first screen has been uploaded for review. Final decision will be made only after all 5 screens are finished.
We hope you give it your best!
Note: will only communicate through PixelHarbor (no skype),
Updates
Reason: Want to give designers a chance to submit their designs as I understand from some, the deadline is too close.
I have raised the award and introduced a 2nd price as well to make it worth your time. I hope you give it your best shot.
Reason: A few of you have asked for an extension of the deadline as time is running out. I will extend by one day. Tell me if you need more.
Industry/Entity Type
Startup
Requirements
Must have
- At least 1 screen before we can give you feedback.
Nice to have
- multiple options of 1 screen to get to a desirable design

```html
<!DOCTYPE html>
<html lang="en">
<head>
<meta charset="utf-8">
<title>Study Dashboard</title>
<link rel="stylesheet" href="https://fonts.googleapis.com/css2?family=Open+Sans:wght@400;600;700;800&display=swap">
<style>
  :root {
    --page-bg: #f4f5f6;
    --header-blue: #2688d4;
    --tile-teal: #0f6f93;
    --tile-divider: rgba(255,255,255,0.35);
    --white: #ffffff;
    --ink: #2b2b2b;
    --pill-grey: #5b5b5b;
    --tab-bg: #f3f3f3;
    --tab-ink: #555555;
    --active-blue: #1f7fd0;
    --gain-green: #b8e84a;
    --loss-red: #f2434a;
  }
  * { box-sizing: border-box; margin: 0; padding: 0; }
  html, body { width: 1200px; height: 1041px; overflow: hidden; }
  body {
    background: var(--page-bg);
    font-family: "Open Sans", Arial, sans-serif;
    display: flex; align-items: center; justify-content: center;
  }
  .app-screen {
    width: 450px; height: 800px;
    background: var(--white);
    display: flex; flex-direction: column;
    box-shadow: 0 10px 40px rgba(0,0,0,0.12);
    overflow: hidden;
  }
  .dashboard-header { background: var(--header-blue); color: var(--white); }
  .status-bar {
    height: 24px; display: flex; align-items: center; justify-content: space-between;
    padding: 0 10px; font-size: 11px; font-weight: 600;
  }
  .status-left, .status-right { display: flex; align-items: center; gap: 6px; width: 120px; }
  .status-right { justify-content: flex-end; }
  .signal-dots { letter-spacing: -1px; font-size: 14px; line-height: 1; }
  .battery { width: 22px; height: 10px; border: 1px solid var(--white); border-radius: 2px; padding: 1px; }
  .battery span { display: block; width: 100%; height: 100%; background: var(--white); }
  .title-row { height: 48px; display: flex; align-items: center; padding: 0 14px; }
  .menu-button { width: 26px; display: flex; flex-direction: column; gap: 5px; }
  .menu-button span { height: 3px; background: var(--white); border-radius: 1px; }
  .welcome { flex: 1; text-align: center; font-size: 19px; font-weight: 600; margin-right: 26px; }
  .score-line {
    display: flex; align-items: baseline; justify-content: center; gap: 12px; height: 82px; padding-top: 4px;
  }
  .score-label { font-size: 36px; font-weight: 400; }
  .score-value { font-size: 64px; font-weight: 800; letter-spacing: 1px; }
  .score-change { font-size: 22px; font-weight: 600; color: var(--loss-red); }
  .stats-row { position: relative; display: flex; align-items: center; height: 58px; padding: 0 26px; }
  .stats-arrow { position: absolute; top: 14px; font-size: 22px; font-weight: 700; }
  .stats-arrow.prev { left: 8px; }
  .stats-arrow.next { right: 8px; }
  .stats-track { display: flex; overflow: hidden; width: 100%; }
  .stat {
    flex: 0 0 118px; text-align: center; border-right: 1px solid var(--tile-divider);
    line-height: 1.2;
  }
  .stat:last-child { border-right: none; }
  .stat-figure { font-size: 16px; font-weight: 700; }
  .stat-figure .pct { color: var(--gain-green); }
  .stat-label { font-size: 12px; }
  .page-dots { display: flex; justify-content: center; gap: 7px; padding: 6px 0 10px; }
  .page-dots span { width: 8px; height: 8px; border-radius: 50%; background: var(--white); }
  .page-dots span.idle { background: transparent; border: 1px solid var(--white); }
  .shortcut-tiles { display: flex; background: var(--tile-teal); color: var(--white); height: 108px; }
  .tile {
    flex: 1; display: flex; flex-direction: column; align-items: center; justify-content: center; gap: 8px;
    border-right: 1px solid var(--tile-divider); font-size: 14px; text-align: center; line-height: 1.2;
  }
  .tile:last-child { border-right: none; }
  .up-next { padding: 30px 24px 0; text-align: center; }
  .up-next-label { font-size: 18px; font-weight: 700; color: var(--ink); margin-bottom: 10px; }
  .up-next-lesson {
    background: var(--pill-grey); color: var(--white); font-size: 22px;
    padding: 12px 10px; border-radius: 3px;
  }
  .spacer { flex: 1; }
  .tab-bar { height: 66px; background: var(--tab-bg); display: flex; border-top: 1px solid #e0e0e0; }
  .tab {
    flex: 1; display: flex; flex-direction: column; align-items: center; justify-content: center; gap: 4px;
    font-size: 11px; font-weight: 600; color: var(--tab-ink);
  }
  .tab.active svg { color: var(--active-blue); }
  svg { display: block; }
</style>
</head>
<body>
<main class="app-screen">
  <header class="dashboard-header">
    <div class="status-bar">
      <div class="status-left"><span class="signal-dots">•••</span><span>ORBIT</span>
        <svg width="12" height="9" viewBox="0 0 12 9" fill="none" stroke="#fff" stroke-width="1.4"><path d="M1 3.5a7 7 0 0 1 10 0M3 5.6a4 4 0 0 1 6 0"/><circle cx="6" cy="7.8" r="0.9" fill="#fff" stroke="none"/></svg>
      </div>
      <span>4:21 PM</span>
      <div class="status-right">
        <svg width="7" height="11" viewBox="0 0 7 11" fill="none" stroke="#fff" stroke-width="1.1"><path d="M1 3l5 5-2.5 2V1L6 3 1 8"/></svg>
        <span>100%</span><div class="battery"><span></span></div>
      </div>
    </div>
    <div class="title-row">
      <div class="menu-button" aria-label="Menu"><span></span><span></span><span></span></div>
      <h1 class="welcome">Welcome back, Rafi</h1>
    </div>
    <div class="score-line">
      <span class="score-label">Score</span>
      <span class="score-value">650</span>
      <span class="score-change">-18</span>
    </div>
    <div class="stats-row">
      <span class="stats-arrow prev">&lsaquo;</span>
      <div class="stats-track">
        <div class="stat"><div class="stat-figure"><span class="pct">34%</span> +4</div><div class="stat-label">Completion</div></div>
        <div class="stat"><div class="stat-figure"><span class="pct">20</span> +3</div><div class="stat-label">Sessions</div></div>
        <div class="stat"><div class="stat-figure"><span class="pct">18</span> +10</div><div class="stat-label">Sessions</div></div>
        <div class="stat"><div class="stat-figure">&nbsp;</div><div class="stat-label">This week</div></div>
      </div>
      <span class="stats-arrow next">&rsaquo;</span>
    </div>
    <div class="page-dots"><span></span><span></span><span></span><span class="idle"></span></div>
  </header>

  <nav class="shortcut-tiles">
    <div class="tile">
      <svg width="30" height="22" viewBox="0 0 30 22" fill="none" stroke="#fff" stroke-width="1.5"><path d="M2 20h26"/><rect x="5" y="12" width="3" height="8"/><rect x="11" y="8" width="3" height="12"/><rect x="17" y="10" width="3" height="10"/><rect x="23" y="5" width="3" height="15"/><path d="M4 9l8-5 6 3 8-5"/></svg>
      <span>Analytics</span>
    </div>
    <div class="tile">
      <svg width="30" height="22" viewBox="0 0 30 22" fill="none" stroke="#fff" stroke-width="1.5"><path d="M15 4c-3-2-8-2-12-1v16c4-1 9-1 12 1 3-2 8-2 12-1V3c-4-1-9-1-12 1zM15 4v16"/></svg>
      <span>Course Overview</span>
    </div>
    <div class="tile">
      <svg width="28" height="24" viewBox="0 0 28 24" fill="none" stroke="#fff" stroke-width="1.5"><rect x="2" y="4" width="22" height="18" rx="1"/><path d="M2 9h22M7 1v5M19 1v5"/><circle cx="20" cy="17" r="5" fill="#0f6f93"/><path d="M20 14.5V17l1.8 1.2"/></svg>
      <span>Days Until<br>Test 33</span>
    </div>
  </nav>

  <section class="up-next">
    <h2 class="up-next-label">Up Next:</h2>
    <div class="up-next-lesson">Sentence Correction Lesson 4</div>
  </section>

  <div class="spacer"></div>

  <nav class="tab-bar">
    <div class="tab">
      <svg width="24" height="20" viewBox="0 0 24 20" fill="currentColor"><path d="M12 2L2 10h3v9h5v-6h4v6h5v-9h3z"/></svg><span>Home</span>
    </div>
    <div class="tab">
      <svg width="26" height="20" viewBox="0 0 26 20" fill="none" stroke="currentColor" stroke-width="1.5"><path d="M13 3c-3-2-7-2-11-1v15c4-1 8-1 11 1 3-2 7-2 11-1V2c-4-1-8-1-11 1zM13 3v15"/></svg><span>Theory</span>
    </div>
    <div class="tab active">
      <svg width="26" height="20" viewBox="0 0 26 20" fill="currentColor"><rect x="2" y="8" width="8" height="10"/><rect x="9" y="5" width="8" height="10"/><rect x="16" y="2" width="8" height="10"/></svg><span>Practice</span>
    </div>
    <div class="tab">
      <svg width="28" height="20" viewBox="0 0 28 20" fill="currentColor"><path d="M7 4h14a5 5 0 0 1 5 6l-1 5a3 3 0 0 1-5 1l-2-2h-8l-2 2a3 3 0 0 1-5-1l-1-5a5 5 0 0 1 5-6z"/><path d="M8 8v4M6 10h4" stroke="#f3f3f3" stroke-width="1.6"/><circle cx="19" cy="9" r="1.2" fill="#f3f3f3"/><circle cx="21" cy="11.5" r="1.2" fill="#f3f3f3"/></svg><span>Games</span>
    </div>
    <div class="tab">
      <svg width="24" height="22" viewBox="0 0 24 22" fill="currentColor"><circle cx="12" cy="11" r="10"/><path d="M7 11l3.5 3.5L17 8" stroke="#f3f3f3" stroke-width="2.2" fill="none"/></svg><span>Test</span>
    </div>
  </nav>
</main>
</body>
</html>
```